Steel Rebar Fabrication Company needs Facebook Ads & page, Instagram Ads & pages designed.

I want to put out an Instagram, Facebook ad, and LinkedIn campaign out for my new company, Ridgeline Metals Inc. I want the ads to be short but clean, clear and precise. I want our address: 4871 Marrowfield Rd. Tsawwassen, BC. I want our hours of operation to be listed 8:00am to 4:00pm Monday to Friday. Product Delivery to your job site or pick up at our yard available. We can cut, bend to custom and standard shapes based upon Canadian CSA Standards. We offer products ranging from 10mm to 35mm diameter Grade 400W rebar. We can bend stirrups, dowels, hairpins; whatever your company needs to complete your product. Whether it is a small project, Tilt Up warehouse, Wood Frame Construction with Concrete parkade foundation; we have the team to meet your needs.
Email address: info@ridgelinemetalsinc.ca
We can service all areas of British Columbia.

Target Market(s)

Construction Company's for homes, condominiums, warehouses, commercial, industrial, and infrastructure projects. As well, as the every day DIY home improvement or renovator.

Industry/Entity Type

Construction

Requirements
Nice to have
• Would like to see a image of the rebar steel that I have provided in the ad. Even if it is in the background with a lower opacity level. Bonus if someone includes any of the movie files I have uploaded.

```html
<!DOCTYPE html>
<html lang="en">
<head>
<meta charset="utf-8">
<title>Ridgeline Metals Inc. — Build Your Dream</title>
<link rel="stylesheet" href="https://fonts.googleapis.com/css2?family=Montserrat:wght@300;400;500;700;800&display=swap">
<style>
  :root {
    --red: #c11d2e;
    --ink: #231f20;
    --panel: #222222;
    --white: #ffffff;
    --steel: #8d9296;
    --steel-dark: #5d6368;
    --text: #2a2a2a;
  }
  * { box-sizing: border-box; margin: 0; padding: 0; }
  html, body { width: 1200px; height: 1200px; overflow: hidden; background: #ffffff; }
  body { font-family: "Montserrat", sans-serif; }
  .ad { position: relative; width: 1200px; height: 1200px; background: var(--white); overflow: hidden; }

  .steel-panel {
    position: absolute; left: 896px; top: 0; width: 304px; height: 1200px;
    background: linear-gradient(180deg, #9a9ea1 0%, #7f868b 45%, #6c7479 70%, #b8bcbe 88%, #7e858a 100%);
  }
  .steel-frame {
    position: absolute; left: 896px; top: 61px; width: 266px; height: 1139px;
    border-top: 2px solid #3d4246; border-right: 2px solid #3d4246;
  }
  .red-stripe { position: absolute; left: 882px; top: 0; width: 14px; height: 1200px; background: var(--red); }

  .brand { position: absolute; left: 44px; top: 44px; width: 320px; text-align: center; color: var(--ink); font-weight: 800; }
  .brand-name { display: block; font-size: 52px; line-height: 1; letter-spacing: 1px; }
  .brand-sub { display: block; font-size: 26px; line-height: 1; margin-top: 12px; letter-spacing: 1px; }

  .kicker { position: absolute; left: 44px; top: 192px; font-size: 26px; font-weight: 400; letter-spacing: 8.5px; color: var(--red); }
  .headline { position: absolute; left: 41px; top: 226px; font-size: 62px; line-height: 60px; font-weight: 800; color: var(--red); }

  .hours {
    position: absolute; left: 0; top: 365px; width: 500px; height: 120px; background: var(--red);
    clip-path: polygon(0 0, 419px 0, 500px 120px, 0 120px);
    color: var(--white);
  }
  .hours-label {
    position: absolute; left: 27px; top: 11px; width: 351px; height: 34px; background: var(--white);
    color: var(--red); font-size: 29px; font-weight: 700; line-height: 34px; padding-left: 17px;
  }
  .hours-time { position: absolute; left: 44px; top: 50px; font-size: 31px; line-height: 34px; font-weight: 700; }
  .hours-time .to { font-weight: 400; }
  .hours-days { position: absolute; left: 44px; top: 84px; font-size: 27px; line-height: 32px; font-weight: 400; }

  .services {
    position: absolute; left: 27px; top: 507px; width: 459px; height: 393px;
    background: var(--panel); border-radius: 22px 22px 0 0; padding: 9px 12px 0 10px;
  }
  .services-title {
    height: 47px; background: var(--red); border-radius: 12px 12px 0 0; color: var(--white);
    font-size: 26px; font-weight: 700; line-height: 47px; padding-left: 56px;
  }
  .services-list { list-style: none; margin-top: 17px; }
  .services-list li { position: relative; padding-left: 39px; color: var(--white); font-size: 17.4px; line-height: 21px; font-weight: 400; margin-bottom: 21px; }
  .services-list svg { position: absolute; left: 6px; top: 3px; }

  .delivery {
    position: absolute; left: 27px; top: 911px; width: 459px; height: 153px; background: var(--red);
    border-radius: 0 0 24px 24px; color: var(--white); text-align: center;
    font-size: 26.5px; line-height: 30px; font-weight: 800; padding-top: 32px;
  }

  .contact-email { position: absolute; left: 48px; top: 1100px; display: flex; align-items: center; gap: 14px; color: var(--text); font-size: 23px; font-weight: 400; white-space: nowrap; }
  .contact-divider { position: absolute; left: 452px; top: 1083px; width: 2px; height: 65px; background: var(--text); }
  .contact-address { position: absolute; left: 480px; top: 1082px; display: flex; gap: 14px; color: var(--text); font-size: 28px; line-height: 44px; font-weight: 400; white-space: nowrap; }
  .contact-address svg { margin-top: 16px; }

  .photo { position: absolute; border-radius: 12px; }
  .photo-towers { left: 526px; top: 115px; width: 596px; height: 652px;
    background: linear-gradient(180deg, #4f9bd8 0%, #9ccbeb 38%, #c9dde6 55%, #8fa7b5 75%, #3f6b34 95%); }
  .photo-aisle { left: 526px; top: 786px; width: 289px; height: 161px;
    background: linear-gradient(90deg, #b9855a 0%, #d9dde0 50%, #b9855a 100%); }
  .photo-forklift { left: 832px; top: 786px; width: 290px; height: 161px;
    background: linear-gradient(90deg, #c89a6a 0%, #e6e8ea 55%, #c89a6a 100%); }

  .service-area {
    position: absolute; left: 526px; top: 977px; width: 341px; height: 76px; background: var(--panel);
    border-radius: 8px; color: var(--white); text-align: center; font-size: 20px; line-height: 25px;
    font-weight: 400; padding-top: 13px;
  }
  .service-area strong { color: var(--red); font-weight: 700; }
</style>
</head>
<body>
<main class="ad">
  <div class="steel-panel" role="img" aria-label="Photo of a modern glass and steel building facade"></div>
  <div class="steel-frame"></div>
  <div class="red-stripe"></div>

  <div class="brand">
    <span class="brand-name">RIDGELINE</span>
    <span class="brand-sub">METALS INC.</span>
  </div>

  <p class="kicker">YOUR CHANCE NOW</p>
  <h1 class="headline">BUILD YOUR<br>DREAM</h1>

  <section class="hours">
    <div class="hours-label">OPERATION HOURS</div>
    <div class="hours-time">8:00AM <span class="to">TO</span> 4:00PM</div>
    <div class="hours-days">MONDAY TO FRIDAY</div>
  </section>

  <section class="services">
    <h2 class="services-title">OUR SERVICES</h2>
    <ul class="services-list">
      <li><svg width="14" height="14" viewBox="0 0 14 14"><rect x="1" y="2" width="11" height="11" fill="none" stroke="#c11d2e" stroke-width="1.6"/><path d="M3.5 7l3 3 7-8" fill="none" stroke="#c11d2e" stroke-width="1.8"/></svg>We can cut, bend to custom and standard shapes based upon Canadian CSA Standards</li>
      <li><svg width="14" height="14" viewBox="0 0 14 14"><rect x="1" y="2" width="11" height="11" fill="none" stroke="#c11d2e" stroke-width="1.6"/><path d="M3.5 7l3 3 7-8" fill="none" stroke="#c11d2e" stroke-width="1.8"/></svg>We can bend stirrups, dowels, hairpins;<br>whatever your company needs to complete your product.</li>
      <li><svg width="14" height="14" viewBox="0 0 14 14"><rect x="1" y="2" width="11" height="11" fill="none" stroke="#c11d2e" stroke-width="1.6"/><path d="M3.5 7l3 3 7-8" fill="none" stroke="#c11d2e" stroke-width="1.8"/></svg>We offer products ranging from 10mm to 35mm diameter Grade400W rebar.</li>
      <li><svg width="14" height="14" viewBox="0 0 14 14"><rect x="1" y="2" width="11" height="11" fill="none" stroke="#c11d2e" stroke-width="1.6"/><path d="M3.5 7l3 3 7-8" fill="none" stroke="#c11d2e" stroke-width="1.8"/></svg>Whether it is a small project, Tilt Up warehouse, Wood Frame Construction with Concrete parkade foundation; we have the team to meet your needs.</li>
    </ul>
  </section>

  <section class="delivery">PRODUCT DELIVERY TO<br>YOUR JOB SITE OR PICK UP<br>AT OUR YARD AVAILABLE</section>

  <div class="contact-email">
    <svg width="40" height="30" viewBox="0 0 40 30"><rect x="0" y="0" width="40" height="30" rx="4" fill="#c11d2e"/><path d="M3 4l17 13 17-13" fill="none" stroke="#ffffff" stroke-width="3"/></svg>
    <span>info@ridgelinemetalsinc.ca</span>
  </div>
  <div class="contact-divider"></div>
  <div class="contact-address">
    <svg width="44" height="52" viewBox="0 0 44 52"><ellipse cx="22" cy="44" rx="20" ry="7" fill="#c11d2e"/><ellipse cx="22" cy="44" rx="12" ry="3.5" fill="#ffffff"/><path d="M22 2a14 14 0 0 1 14 14c0 10-14 26-14 26S8 26 8 16A14 14 0 0 1 22 2z" fill="#c11d2e"/><circle cx="22" cy="16" r="6" fill="#ffffff"/></svg>
    <span>4871 Marrowfield<br>Rd. Tsawwassen, BC.</span>
  </div>

  <div class="photo photo-towers" role="img" aria-label="Photo of twin curved glass skyscrapers against a blue sky above green trees"></div>
  <div class="photo photo-aisle" role="img" aria-label="Photo of a warehouse aisle lined with shelves of boxes"></div>
  <div class="photo photo-forklift" role="img" aria-label="Photo of a forklift carrying boxes in a warehouse"></div>

  <div class="service-area">WE CAN SERVICE ALL AREAS<br>OF <strong>BRITISH COLUMBIA</strong></div>
</main>
</body>
</html>
```